HushHarbors.com

Updated Website Structure for HushHarbor.com
1. Home Page

(Add social media links in footer or sidebar)
Suggested addition:

Stay Connected
Follow Hush Harbor for daily encouragement, calming tools, and community stories.

[Facebook Icon] [Instagram Icon] [YouTube Icon]
@HushHarborOfficial

2. How It Works

(No major change — keep focused on process and trust building)

3. Ebook Store

(Add social links at the bottom of the page)

Want more free content?
Follow us on social media for sneak peeks, affirmations, and updates on new releases!

[Facebook] [Instagram] [YouTube]

4. Certification Page

(Optional social proof addition)

Connect with Certified Hush Harbors
Join our online community and see real stories of growth and courage.

Follow us on social media to see how others are supporting each other:

5. Membership Tiers

(Keep page simple, but can include icons in footer)

6. About Me

Suggested addition:

Let’s Stay Connected
I love hearing from others walking this path.

Facebook: @HushHarborOfficial

Instagram: @HushHarborOfficial

YouTube: Hush Harbor Channel

7. Disclosure Page

(Keep links in footer only for professional feel.)

8. Global Footer (Site-wide)

Every page should include a calming footer with:

Navigation links (Home | About Me | How It Works | Ebook Store | Certification | Membership | Disclosure)

Social media icons

Copyright info

Example footer text:

🌿 Walking with fear, choosing courage, calming the nervous system together.

© 2025 HushHarbor.com | All rights reserved

```html
<!DOCTYPE html>
<html lang="en">
<head>
<meta charset="utf-8">
<title>Hush Harbors — Walking with fear, choosing courage</title>
<link rel="stylesheet" href="https://fonts.googleapis.com/css2?family=Playfair+Display:wght@400;500;700&family=Manrope:wght@400;500&family=Great+Vibes&display=swap">
<style>
  :root{
    --plum:#2d0229;
    --pink:#eac6e6;
    --pink-line:#d9a2d3;
    --ink:#1e1a1d;
    --white:#ffffff;
    --watermark:#f1eff0;
  }
  *{box-sizing:border-box;margin:0;padding:0}
  html,body{width:1200px;height:2537px;overflow:hidden;background:var(--white)}
  body{position:relative;font-family:"Manrope",sans-serif;color:var(--ink)}
  a{color:inherit;text-decoration:none}

  /* header */
  .site-header{position:absolute;top:0;left:0;width:1200px;height:88px;background:var(--white)}
  .brand{position:absolute;left:103px;top:27px;font-family:"Playfair Display",serif;font-weight:500;font-size:22px;color:var(--plum);white-space:nowrap}
  .main-nav{position:absolute;right:101px;top:22px;display:flex;align-items:center;gap:33px;font-family:"Playfair Display",serif;font-size:15px;color:var(--plum);white-space:nowrap}
  .nav-pill{background:var(--pink);border-radius:21px;width:166px;height:40px;display:flex;align-items:center;justify-content:center;font-size:16px}

  /* hero */
  .hero{position:absolute;top:88px;left:0;width:1200px;height:642px;
    background:linear-gradient(180deg,#2e0a2a 0%,#4c3648 22%,#8a7a7a 36%,#6d7590 48%,#3a4257 64%,#1b1d24 85%,#15161b 100%)}
  .hero h1{position:absolute;top:224px;width:100%;text-align:center;font-family:"Playfair Display",serif;font-weight:400;font-size:44px;color:var(--white);white-space:nowrap}
  .btn{display:inline-flex;align-items:center;justify-content:space-between;background:var(--pink);border-radius:21px;height:40px;padding:0 2px 0 18px;font-family:"Playfair Display",serif;font-size:17px;color:var(--plum);white-space:nowrap}
  .btn .arrow{flex:none;width:36px;height:36px;border-radius:50%;background:var(--plum);display:flex;align-items:center;justify-content:center;margin-left:14px}
  .hero .btn{position:absolute;top:305px;left:522px;width:155px}

  /* stay connected */
  .stay{position:absolute;top:730px;left:0;width:1200px;height:117px;background:var(--plum);color:var(--white)}
  .stay h2{position:absolute;left:101px;top:20px;font-family:"Playfair Display",serif;font-weight:400;font-size:33px;white-space:nowrap}
  .stay p{position:absolute;left:101px;top:70px;font-size:17px;white-space:nowrap}
  .social-row{position:absolute;top:35px;left:911px;display:flex;gap:13px}
  .social-row span{width:53px;height:53px;border-radius:50%;background:var(--white);display:flex;align-items:center;justify-content:center}

  /* about */
  .about-script{position:absolute;left:101px;top:935px;font-family:"Great Vibes",cursive;font-size:150px;color:var(--watermark);line-height:1;white-space:nowrap}
  .about-copy{position:absolute;left:166px;top:1050px;width:465px}
  .about-copy h2{font-family:"Playfair Display",serif;font-weight:400;font-size:33px;color:var(--plum)}
  .rule{display:block;width:52px;height:2px;background:var(--pink-line)}
  .about-copy .rule{margin:12px 0 24px}
  .about-copy p{font-size:16px;line-height:27px;text-align:justify;color:#2b2b2b}
  .about-copy .btn{margin-top:20px;width:156px}
  .about-photo{position:absolute;left:688px;top:907px;width:406px;height:431px;background:linear-gradient(160deg,#e8e4df 0%,#d6b6a6 45%,#b32a2e 100%)}

  /* helps */
  .helps-title{position:absolute;top:1392px;width:100%;text-align:center;font-family:"Playfair Display",serif;font-weight:400;font-size:34px;color:var(--plum)}
  .helps-rule{position:absolute;top:1446px;left:574px}
  .helps-intro{position:absolute;top:1462px;left:255px;width:690px;text-align:center;font-size:16px;line-height:23px;color:#2b2b2b}
  .card{position:absolute;top:1534px;width:326px;height:347px}
  .card-frame{position:absolute;left:67px;top:71px;width:192px;height:206px;border:1px solid rgba(255,255,255,.85);display:flex;flex-direction:column;align-items:center;justify-content:center;padding-top:30px;color:var(--white);font-family:"Playfair Display",serif;font-size:16px}
  .card-frame svg{margin-bottom:8px}
  .card-support{left:103px;background:linear-gradient(135deg,#d9cfc5,#c9a898 55%,#8a9bb0)}
  .card-tools{left:438px;background:linear-gradient(180deg,#d4d4d2 0%,#b8ae96 50%,#a8873f 100%)}
  .card-calm{left:773px;background:linear-gradient(180deg,#b8c4c8 0%,#7d8e98 50%,#3e5364 100%)}

  /* connect */
  .connect{position:absolute;top:1960px;left:0;width:1200px;height:258px;background:linear-gradient(180deg,#3e1538,#5a2a4e 60%,#4a2042);color:var(--white);text-align:center}
  .connect h2{margin-top:50px;font-family:"Playfair Display",serif;font-weight:400;font-size:33px;white-space:nowrap}
  .connect .rule{background:var(--white);margin:12px auto 15px}
  .connect p{font-size:16px}
  .signup{position:absolute;left:283px;top:163px;width:633px;height:43px;border-radius:22px;background:var(--white);display:flex;align-items:center;justify-content:space-between;padding:0 2px 0 24px}
  .signup span{font-size:15px;color:#333}
  .signup b{width:160px;height:39px;border-radius:20px;background:var(--plum);font-family:"Playfair Display",serif;font-weight:400;font-size:17px;display:flex;align-items:center;justify-content:center}

  /* footer */
  .footer-brand{position:absolute;left:101px;top:2263px;width:201px;height:174px;display:flex;align-items:center;justify-content:center;font-family:"Playfair Display",serif;font-weight:500;font-size:28px;color:var(--plum);white-space:nowrap}
  .footer-col{position:absolute;top:2270px;font-size:16px;color:#222;white-space:nowrap}
  .footer-col h3{font-family:"Playfair Display",serif;font-weight:700;font-size:17px;color:var(--plum);margin-bottom:4px}
  .footer-col li{list-style:none;line-height:28.5px}
  .col-forms{left:417px}
  .col-location{left:642px}
  .col-location p{line-height:26px}
  .col-call{left:909px}
  .col-call h3.second{margin-top:14px}
  .footer-social{display:flex;gap:12px;margin-top:16px}
  .footer-social span{width:35px;height:35px;border-radius:50%;background:var(--plum);display:flex;align-items:center;justify-content:center}
  .footer-divider{position:absolute;left:101px;top:2463px;width:997px;height:1px;background:#e6dce4}
  .legal{position:absolute;top:2503px;font-size:16px;line-height:20px;color:#222;white-space:nowrap}
  .legal-left{left:101px}
  .legal-right{right:105px}
</style>
</head>
<body>

<header class="site-header">
  <div class="brand">Hush Harbors</div>
  <nav class="main-nav">
    <a>Home</a><a>About Me</a><a>How It Works</a><a>Ebook Store</a><a>Certification</a>
    <a class="nav-pill">Membership</a>
  </nav>
</header>

<section class="hero" role="img" aria-label="Misty mountain range at sunrise under a dark purple sky">
  <h1>Walking with fear, choosing courage</h1>
  <a class="btn">Get Started<span class="arrow"><svg width="18" height="14" viewBox="0 0 18 14"><path d="M1 7h15M10 1l6 6-6 6" fill="none" stroke="#fff" stroke-width="1.8"/></svg></span></a>
</section>

<section class="stay">
  <h2>Stay Connected</h2>
  <p>Follow Hush Harbor for daily encouragement, calming tools, and community stories.</p>
  <div class="social-row" aria-label="Social media links">
    <span><svg width="24" height="24" viewBox="0 0 24 24" fill="none" stroke="#2d0229" stroke-width="2"><path d="M4 5h16v11H9l-5 4z"/></svg></span>
    <span><svg width="24" height="24" viewBox="0 0 24 24" fill="#2d0229"><path d="M12 21s-8-5.2-8-11a4.5 4.5 0 0 1 8-2.8A4.5 4.5 0 0 1 20 10c0 5.8-8 11-8 11z"/></svg></span>
    <span><svg width="24" height="24" viewBox="0 0 24 24" fill="none" stroke="#2d0229" stroke-width="2"><circle cx="18" cy="5" r="2.5"/><circle cx="6" cy="12" r="2.5"/><circle cx="18" cy="19" r="2.5"/><path d="M8.2 10.8l7.6-4.6M8.2 13.2l7.6 4.6"/></svg></span>
  </div>
</section>

<div class="about-script" aria-hidden="true">About Me</div>
<section class="about-copy">
  <h2>About Me</h2>
  <span class="rule"></span>
  <p>Lorem ipsum dolor sit amet, consectetur adipiscing elit, sed do eiusmod tempor incididunt ut labore et dolore magna aliqua. Ut enim ad minim veniam, quis nostrud exercitation ullamco laboris nisi ut aliquip ex ea commodo consequat.</p>
  <a class="btn">Learn More<span class="arrow"><svg width="18" height="14" viewBox="0 0 18 14"><path d="M1 7h15M10 1l6 6-6 6" fill="none" stroke="#fff" stroke-width="1.8"/></svg></span></a>
</section>
<div class="about-photo" role="img" aria-label="Portrait of the founder in red glasses and a red floral shirt"></div>

<h2 class="helps-title">Hush Harbor Helps You</h2>
<span class="rule helps-rule"></span>
<p class="helps-intro">Lorem ipsum dolor sit amet, consectetur adipiscing elit, sed do eiusmod tempor incididunt ut labore et dolore magna aliqua. Ut enim ad minim veniam</p>

<div class="card card-support" role="img" aria-label="Two people holding hands in support">
  <div class="card-frame"><svg width="34" height="34" viewBox="0 0 34 34" fill="none" stroke="#fff" stroke-width="1.5"><path d="M8 28l6-12 5 6M26 28l-6-12-5 6"/><path d="M17 4v5M9 7l3 4M25 7l-3 4"/></svg>Support</div>
</div>
<div class="card card-tools" role="img" aria-label="Woman sitting in a golden grass field">
  <div class="card-frame"><svg width="30" height="34" viewBox="0 0 30 34" fill="none" stroke="#fff" stroke-width="1.5"><rect x="8" y="16" width="14" height="16" rx="2"/><path d="M11 16V5M15 16V3M19 16V6"/></svg>Tools</div>
</div>
<div class="card card-calm" role="img" aria-label="Person meditating by the water at sunset">
  <div class="card-frame"><svg width="36" height="34" viewBox="0 0 36 34" fill="none" stroke="#fff" stroke-width="1.5"><circle cx="18" cy="16" r="13"/><path d="M18 8c-4 4-4 10 0 14 4-4 4-10 0-14zM10 14c1 5 4 8 8 8M26 14c-1 5-4 8-8 8"/></svg>Calm Mind</div>
</div>

<section class="connect" role="region" aria-label="Community signup over a dusky landscape">
  <h2>Connect With Certified Hush Harbors</h2>
  <span class="rule"></span>
  <p>Join our online community and see real stories of growth and courage.</p>
  <div class="signup"><span>Email address</span><b>Join Us</b></div>
</section>

<div class="footer-brand">Hush Harbors</div>
<div class="footer-col col-forms">
  <h3>Forms</h3>
  <ul><li>Home</li><li>About Me</li><li>How It Works</li><li>Ebook Store</li></ul>
</div>
<div class="footer-col col-location">
  <h3>Location</h3>
  <p>1234 Main Rd<br>Somewhere, US 12345</p>
</div>
<div class="footer-col col-call">
  <h3>Call Us</h3>
  <p>+1 888 888 8888</p>
  <h3 class="second">Email</h3>
  <p>info@HushHarbor.com</p>
  <div class="footer-social" aria-label="Social media links">
    <span><svg width="16" height="16" viewBox="0 0 24 24" fill="none" stroke="#fff" stroke-width="2.4"><path d="M4 5h16v11H9l-5 4z"/></svg></span>
    <span><svg width="16" height="16" viewBox="0 0 24 24" fill="#fff"><path d="M12 21s-8-5.2-8-11a4.5 4.5 0 0 1 8-2.8A4.5 4.5 0 0 1 20 10c0 5.8-8 11-8 11z"/></svg></span>
    <span><svg width="16" height="16" viewBox="0 0 24 24" fill="none" stroke="#fff" stroke-width="2.4"><circle cx="18" cy="5" r="2.5"/><circle cx="6" cy="12" r="2.5"/><circle cx="18" cy="19" r="2.5"/><path d="M8.2 10.8l7.6-4.6M8.2 13.2l7.6 4.6"/></svg></span>
  </div>
</div>
<div class="footer-divider"></div>
<p class="legal legal-left">Copyright ©2025 HushHarbors. All Rights Reserved.</p>
<p class="legal legal-right">Certification I Membership I Disclosure</p>

</body>
</html>
```